Healthy lifestyle Influencer business card

I need your creativity to have a business card that I can leave in all the restaurants, hotels and spas I visit to inform them that I am an influencer specializing in the wellness sector and that I will write a review about them. You can use my instagram photos Lunavita27 or on my website www.piattileggeriorto.it. I would like my business card to impress with its creativity! thank you very much!

Contact Information for Business Card

siteweb, instagram, phone number

Font styles to use
Decorative
Script

Colors
0094D4
00A9DD
6FCCEA
C7EBF8
E9F6FB
59FF00
82FF00
B8FF75
E3FFCB
F4FFEA
FFC000
F8CF3A
FAE287
FDF2CF
FEFAEE
F0912C
F2A743
F7CA91
FBE8D2
FDF5EE
EE7325
F08F49
F5BC92
FAE3D3
FDF4ED
EB3D1F
EC4F4E
F09395
F8D3D4
FCEDEE
E54698
E96AAD
F1A4CE
F9D9EA
FCEFF6

Requirements
Nice to have
• creativity

```html
<!DOCTYPE html>
<html lang="it">
<head>
<meta charset="utf-8">
<title>Luna Vita Chef – Biglietto da visita</title>
<link rel="stylesheet" href="https://fonts.googleapis.com/css2?family=Great+Vibes&family=Quicksand:wght@500&family=Roboto:wght@300;400&display=swap">
<style>
  :root{
    --page:#2b2b2b;
    --sage-top:#a2c6bb;
    --sage-bottom:#8cb2a6;
    --paper-top:#f7f7f6;
    --paper-bottom:#e4e4e3;
    --ink:#454545;
    --ink-soft:#5a5a5a;
    --icon:#8fb7aa;
    --kiwi-green:#7fae3a;
    --kiwi-brown:#8a6a3c;
  }
  *{margin:0;padding:0;box-sizing:border-box}
  html,body{width:1200px;height:1138px;overflow:hidden;background:var(--page)}
  .card{position:absolute;width:620px;height:375px;border-radius:20px;overflow:hidden}
  .card--front{left:272px;top:184px;background:linear-gradient(180deg,var(--sage-top),var(--sage-bottom))}
  .card--back{left:274px;top:606px;background:linear-gradient(180deg,var(--paper-top),var(--paper-bottom))}

  .gallery{position:absolute;left:24px;top:23px;display:grid;grid-template-columns:repeat(3,185px);grid-template-rows:repeat(2,103px);column-gap:10px;row-gap:9px}
  .gallery__photo{border-radius:2px}
  .photo--mousse{background:linear-gradient(135deg,#e9e7e8,#a98a80)}
  .photo--velvet{background:linear-gradient(135deg,#c25a4e,#f1e2cf 55%,#d9a08f)}
  .photo--parfait{background:linear-gradient(135deg,#6e5438,#35508d 60%,#b89d78)}
  .photo--berry-tart{background:linear-gradient(180deg,#3c4660,#d9bfc8 60%,#eeeeee)}
  .photo--batter{background:radial-gradient(circle at 50% 40%,#c98f62 45%,#6b4a2b 80%)}
  .photo--macaroons{background:linear-gradient(135deg,#f1f0ef,#e6c59a 55%,#d8a86c)}

  .brand{position:absolute;text-align:center;color:var(--ink)}
  .brand__name{font-family:"Quicksand",sans-serif;font-weight:500;letter-spacing:.5px}
  .brand__tagline{font-family:"Quicksand",sans-serif;font-weight:500;color:var(--ink-soft)}
  .card--front .brand{left:0;right:0;top:276px}
  .card--front .brand__name{font-size:30px;line-height:36px}
  .card--front .brand__tagline{font-size:13px;margin-top:8px}
  .card--back .brand{left:40px;width:282px;top:150px}
  .card--back .brand__name{font-size:34px;line-height:40px}
  .card--back .brand__tagline{font-size:15px;margin-top:10px}

  .kiwi{position:absolute;background:radial-gradient(circle at 45% 45%,#dfe9a8 10%,var(--kiwi-green) 35%,#4f7f2a 60%,var(--kiwi-brown) 75%)}
  .kiwi--top{right:0;top:0;width:118px;height:134px;border-radius:0 0 0 70%}
  .kiwi--bottom{left:0;bottom:0;width:118px;height:137px;border-radius:0 70% 0 0}

  .contact{position:absolute;left:344px;top:118px;color:var(--ink-soft);font-family:"Roboto",sans-serif;font-weight:300}
  .contact__name{font-family:"Great Vibes",cursive;font-size:27px;color:var(--ink);margin-bottom:8px}
  .contact__list{list-style:none}
  .contact__item{display:flex;align-items:center;gap:6px;font-size:15px;height:21px;margin-left:12px}
  .contact__item svg{width:12px;height:12px;fill:none;stroke:var(--icon);stroke-width:1.6}
  .contact__vat{font-size:15px;margin:10px 0 0 9px}

  .social{position:absolute;left:266px;top:324px;display:flex;align-items:center;gap:9px;font-family:"Roboto",sans-serif;font-weight:300;font-size:17px;color:var(--ink-soft)}
  .social__dot{width:13px;height:13px;border-radius:50%;background:var(--icon)}
</style>
</head>
<body>
  <section class="card card--front">
    <div class="gallery">
      <div class="gallery__photo photo--mousse" role="img" aria-label="Foto di mousse al cioccolato in ciotole di vetro"></div>
      <div class="gallery__photo photo--velvet" role="img" aria-label="Foto di torta red velvet tagliata"></div>
      <div class="gallery__photo photo--parfait" role="img" aria-label="Foto di bicchierino con frutti di bosco"></div>
      <div class="gallery__photo photo--berry-tart" role="img" aria-label="Foto di cheesecake ai mirtilli"></div>
      <div class="gallery__photo photo--batter" role="img" aria-label="Foto di impasto in teglia apribile"></div>
      <div class="gallery__photo photo--macaroons" role="img" aria-label="Foto di biscotti al cocco"></div>
    </div>
    <div class="brand">
      <p class="brand__name">Luna Vita Chef</p>
      <p class="brand__tagline">Leggera con i piatti che ami</p>
    </div>
  </section>

  <section class="card card--back">
    <div class="kiwi kiwi--top" role="img" aria-label="Illustrazione di kiwi con foglie"></div>
    <div class="kiwi kiwi--bottom" role="img" aria-label="Illustrazione di kiwi con foglie"></div>

    <div class="brand">
      <p class="brand__name">Luna Vita Chef</p>
      <p class="brand__tagline">Leggera con i piatti che ami</p>
    </div>

    <div class="contact">
      <p class="contact__name">Luna Martelli</p>
      <ul class="contact__list">
        <li class="contact__item">
          <svg viewBox="0 0 12 12"><path d="M2 3.5c0-1 .8-1.5 4-1.5s4 .5 4 1.5M3 5h6l1 5H2z"/></svg>
          000-0000-0000
        </li>
        <li class="contact__item">
          <svg viewBox="0 0 12 12"><rect x="1" y="2.5" width="10" height="7"/><path d="M1 2.5l5 4 5-4"/></svg>
          info@piattileggeriorto.it
        </li>
        <li class="contact__item">
          <svg viewBox="0 0 12 12"><circle cx="6" cy="6" r="5"/><path d="M1 6h10M6 1c-2.5 3-2.5 7 0 10M6 1c2.5 3 2.5 7 0 10"/></svg>
          www.piattileggeriorto.it
        </li>
      </ul>
      <p class="contact__vat">Partita IVA 01234567890</p>
    </div>

    <div class="social">
      <span class="social__dot"></span>
      <span>@Lunavita27</span>
    </div>
  </section>
</body>
</html>
```